House flipping business web site needed

pinecrestholdingsgroup.example.
I am a residential developer in Northern NJ and I am looking for a fresh new updated website. I have an intro video about my company being made now. I don't update it very often but I want an easy format that I can add update photos to on projects I have worked on or homes I renovate for sale.

Target Market(s)

investors into my projects so a portfolio , people looking to sell their homes to me.

Industry/Entity Type

Real Estate Development

Number of Pages Required

4 page

Font styles to use
Serif

Colors
33b8a4
39a9d7
cadf82

Requirements
Must have
• space for an intro video about my company
• a portfolio with pictures and information about each project
• Markets we serve- Morris County, NJ
• My logo- already created
• SEO
• Yes I would like this to function over all platforms. Phone, computer, all platforms.
• history and background page
• I am looking for a completed page that I can upload to the site that hosts my website
Nice to have
• I want something creative, easy to navigate. modern.

```html
<!DOCTYPE html>
<html lang="en">
<head>
<meta charset="utf-8">
<title>Pinecrest Holdings Group – Home Buying &amp; Renovation</title>
<link rel="stylesheet" href="https://fonts.googleapis.com/css2?family=Lato:wght@400;700&family=Open+Sans:wght@400;600&family=Parisienne&display=swap">
<style>
:root{
  --green:#8cc63f;
  --navy:#2f5a80;
  --navy-dark:#345d83;
  --blue:#2fa3e0;
  --sand:#f1ead4;
  --mint:#e9f1dc;
  --text:#555;
  --muted:#777;
  --line:#d8d8d8;
  --white:#fff;
}
*{box-sizing:border-box;margin:0;padding:0}
html,body{width:1200px;height:2384px;overflow:hidden;background:var(--white)}
body{position:relative;font-family:"Open Sans",Arial,sans-serif;color:var(--text)}
.abs{position:absolute}
.script{font-family:"Parisienne",cursive;font-weight:400}

/* top bar */
.topbar{left:0;top:0;width:1200px;height:52px;background:var(--green);color:var(--white);font-size:17px}
.topbar .item{position:absolute;top:0;height:52px;display:flex;align-items:center;gap:14px}
.topbar .sep{position:absolute;left:246px;top:0;width:1px;height:52px;background:rgba(255,255,255,.35)}
.topbar .social{position:absolute;right:78px;top:17px;display:flex;gap:18px}
.topbar .social span{width:18px;height:18px;border-radius:50%;background:rgba(255,255,255,.8)}

/* header */
.brand{left:78px;top:56px;width:194px;height:135px;background:#f4f4f4;display:flex;flex-direction:column;align-items:center;justify-content:center;gap:10px}
.brand .mark{width:30px;height:30px;background:var(--green)}
.brand .name{font-family:"Lato",sans-serif;font-weight:700;color:var(--navy);font-size:17px;text-align:center;line-height:1.2}
.nav a{position:absolute;top:112px;font-family:"Lato",sans-serif;font-size:20px;color:#444;text-decoration:none;transform:translateX(-50%);letter-spacing:.3px}
.nav a.active{color:var(--blue)}
.nav .underline{position:absolute;left:434px;top:150px;width:92px;height:3px;background:var(--green)}

/* hero */
.hero{left:0;top:192px;width:1200px;height:574px;background:linear-gradient(180deg,#3e6a95 0%,#6f8eac 35%,#8a6a4e 55%,#2f5778 78%,#4a6b3a 100%)}
.hero h1{position:absolute;left:80px;top:318px;font-family:"Lato",sans-serif;font-weight:700;color:var(--white);font-size:47px;line-height:68px;letter-spacing:-.5px;white-space:nowrap}

/* about */
.about-title{left:80px;top:815px;font-size:40px;color:var(--green);white-space:nowrap}
.about-title b{font-weight:400;color:var(--navy)}
.about-rule{left:80px;top:876px;width:480px;height:1px;background:var(--line)}
.about-rule::before{content:"";position:absolute;left:0;top:-1px;width:125px;height:3px;background:#b8b8b8}
.about-text{left:80px;top:889px;width:610px;font-size:15.5px;line-height:25px;color:var(--text)}
.about-more{left:548px;top:996px;font-size:18px;color:var(--green)}
.video-card{left:710px;top:715px;width:412px;height:302px;background:var(--white);box-shadow:0 2px 10px rgba(0,0,0,.3)}
.video-card h3{position:absolute;left:18px;top:18px;font-size:28px;color:var(--green);white-space:nowrap}
.video-card h3 b{font-weight:400;color:var(--navy)}
.video{position:absolute;left:15px;top:68px;width:384px;height:220px;background:linear-gradient(135deg,#2a2a2a,#5a5048 60%,#2b2b2b)}
.video svg{position:absolute;left:170px;top:88px}

/* gallery */
.gallery{left:0;top:1074px;width:1200px;height:364px;background:var(--sand)}
.gallery h2{position:absolute;left:0;width:1200px;top:52px;text-align:center;font-size:50px;color:var(--green)}
.gallery h2 b{font-weight:400;color:var(--navy)}
.thumb{position:absolute;top:134px;width:229px;height:133px;border:3px solid #111}
.thumb-line{position:absolute;top:296px;width:229px;height:1px;background:#8aa}
.thumb-line.first{background:var(--green)}
.thumb .caption{position:absolute;left:38px;top:26px;width:170px;color:var(--white);font-size:14px;line-height:22px;text-align:center}
.thumb .frame{position:absolute;left:40px;top:6px;width:180px;height:110px;border:1px solid rgba(255,255,255,.7)}
.arrow{position:absolute;top:180px}

/* services */
.service{top:1438px;width:320px}
.service h3{position:absolute;top:50px;font-size:40px;color:var(--green);white-space:nowrap}
.service h3 b{font-weight:400;color:var(--navy)}
.service .icon{position:absolute;top:136px}
.service p{position:absolute;top:234px;width:300px;font-size:15.5px;line-height:25px}
.btn-outline{position:absolute;top:329px;width:156px;height:46px;border:1.5px solid var(--green);border-radius:23px;color:var(--navy);font-family:"Lato",sans-serif;font-size:19px;display:flex;align-items:center;justify-content:center}
.divider{position:absolute;top:1486px;width:1px;height:341px;background:var(--line)}
.divider::before{content:"";position:absolute;left:-1px;top:0;width:3px;height:44px;background:var(--green)}

/* contact band */
.contact-band{left:0;top:1851px;width:1200px;height:156px;background:var(--mint)}
.contact-shape{position:absolute;left:0;top:0}
.contact-title{position:absolute;left:80px;top:22px;width:240px;font-size:42px;line-height:56px;color:#111;white-space:nowrap}
.field{position:absolute;border:1px solid #cfd9c2;border-radius:3px;background:#eef4e6;font-size:14px;color:#888;padding:10px 12px}
.submit{position:absolute;left:961px;top:81px;width:154px;height:44px;border-radius:22px;background:var(--navy-dark);color:var(--white);font-family:"Lato",sans-serif;font-size:21px;display:flex;align-items:center;justify-content:center}

/* footer */
.foot-head{top:2060px;font-size:22px;color:var(--green);white-space:nowrap}
.foot-head b{font-weight:400;color:var(--navy)}
.foot-row{position:absolute;display:flex;gap:18px;font-size:15.5px;line-height:24px;color:var(--muted)}
.foot-row strong{font-weight:400;color:#333}
.foot-brand{left:520px;top:2061px;width:162px;height:122px;background:#f4f4f4;display:flex;flex-direction:column;align-items:center;justify-content:center;gap:8px}
.foot-brand .mark{width:24px;height:24px;background:var(--green)}
.foot-brand .name{font-family:"Lato",sans-serif;font-weight:700;color:var(--navy);font-size:15px;text-align:center;line-height:1.2}
.foot-tagline{left:460px;top:2198px;width:282px;text-align:center;font-size:16px;line-height:25px;color:var(--muted);text-transform:uppercase}
.social-row{position:absolute;left:890px;display:flex;align-items:center;gap:14px;font-size:16px;color:#333}
.social-row .dot{width:52px;height:52px;border-radius:50%;border:1.5px solid var(--blue)}
.social-row .dot.filled{background:var(--blue)}
.social-row.first span{color:var(--blue)}
.copyright{left:0;top:2333px;width:1200px;height:51px;background:var(--green);color:var(--white);font-size:15.5px;display:flex;align-items:center;justify-content:center}
.copyright strong{margin:0 4px}
</style>
</head>
<body>

<div class="abs topbar">
  <div class="item" style="left:78px">
    <svg width="16" height="28" viewBox="0 0 16 28"><rect x="1" y="1" width="14" height="26" rx="3" fill="none" stroke="#fff" stroke-width="2"/><circle cx="8" cy="23" r="1.5" fill="#fff"/></svg>
    123 456 7890
  </div>
  <div class="sep"></div>
  <div class="item" style="left:268px">
    <svg width="30" height="22" viewBox="0 0 30 22"><rect x="1" y="1" width="28" height="20" rx="3" fill="none" stroke="#fff" stroke-width="2"/><path d="M2 3l13 10L28 3" fill="none" stroke="#fff" stroke-width="2"/></svg>
    hello@pinecrestholdingsgroup.example
  </div>
  <div class="social"><span></span><span></span><span></span></div>
</div>

<div class="abs brand">
  <div class="mark"></div>
  <div class="name">PINECREST<br>HOLDINGS GROUP</div>
</div>

<nav class="nav">
  <a class="active" href="#" style="left:480px">HOME</a>
  <a href="#" style="left:661px">ABOUT</a>
  <a href="#" style="left:861px">PORTFOLIO</a>
  <a href="#" style="left:1077px">CONTACT</a>
  <div class="underline"></div>
</nav>

<section class="abs hero" role="img" aria-label="Photo of a modern timber house with a long pool at dusk">
  <h1>WE BRING EXCELLENCE TO THE<br>HOME BUYING AND<br>RENOVATION BUSINESS.</h1>
</section>

<h2 class="abs script about-title">About <b>Pinecrest Holdings Group</b></h2>
<div class="abs about-rule"></div>
<p class="abs about-text">Pinecrest Holdings Group is a family run business with 3rd generation builders and renovators in the Morris County area. As the President and owner of Pinecrest Holdings Group I am dedicated to working hard to create opportunities for investment through real estate.</p>
<div class="abs script about-more">Read More »</div>

<div class="abs video-card">
  <h3 class="script">About <b>Our Company</b></h3>
  <div class="video" role="img" aria-label="Company intro video still of the team in an office">
    <svg width="46" height="46" viewBox="0 0 46 46"><circle cx="23" cy="23" r="23" fill="#fff"/><path d="M18 13l14 10-14 10z" fill="#111"/></svg>
  </div>
</div>

<section class="abs gallery">
  <h2 class="script">Projects <b>Gallery</b></h2>
  <svg class="arrow" style="left:36px" width="40" height="40" viewBox="0 0 40 40"><path d="M20 4L6 20l14 16M34 4L20 20l14 16" fill="none" stroke="#111" stroke-width="4"/></svg>
  <svg class="arrow" style="left:1124px" width="40" height="40" viewBox="0 0 40 40"><path d="M6 4l14 16L6 36M20 4l14 16-14 16" fill="none" stroke="#111" stroke-width="4"/></svg>

  <div class="thumb" style="left:108px;background:#1f2a3a" role="img" aria-label="Project photo">
    <div class="frame"></div>
    <div class="caption">Lorem Ipsum is simply dummy text...<br>READ MORE»</div>
  </div>
  <div class="thumb" style="left:357px;background:linear-gradient(180deg,#d8c2a4,#a0552a)" role="img" aria-label="Renovated interior with wood floors and fireplace"></div>
  <div class="thumb" style="left:607px;background:linear-gradient(180deg,#5f95d6 0%,#6a7f7a 50%,#3f5a4a 100%)" role="img" aria-label="Blue-green two storey house exterior"></div>
  <div class="thumb" style="left:858px;background:linear-gradient(180deg,#b8c4cf 0%,#8a7a68 60%,#6d5e4e 100%)" role="img" aria-label="Small house before renovation"></div>

  <div class="thumb-line first" style="left:108px"></div>
  <div class="thumb-line" style="left:357px"></div>
  <div class="thumb-line" style="left:607px"></div>
  <div class="thumb-line" style="left:858px"></div>
</section>

<section class="abs service" style="left:80px">
  <h3 class="script">How we can <b>help</b></h3>
  <svg class="icon" style="left:102px" width="82" height="82" viewBox="0 0 82 82"><circle cx="41" cy="41" r="38" fill="none" stroke="#2f5a80" stroke-width="3.5"/><path d="M30 32a11 11 0 1 1 15 10c-3 1.5-4 3-4 7v3" fill="none" stroke="#2f5a80" stroke-width="4" stroke-linecap="round"/><circle cx="41" cy="61" r="2.8" fill="#2f5a80"/></svg>
  <p>Do you need to sell your home fast to avoid foreclosure, have estate home you do not want to fix to put on the market...</p>
  <div class="btn-outline" style="left:72px">READ MORE</div>
</section>
<div class="divider" style="left:405px"></div>

<section class="abs service" style="left:427px">
  <h3 class="script">Financing</h3>
  <svg class="icon" style="left:110px" width="82" height="82" viewBox="0 0 82 82"><circle cx="41" cy="41" r="38" fill="none" stroke="#2f5a80" stroke-width="3.5"/><circle cx="41" cy="41" r="29" fill="#2f5a80"/><text x="41" y="54" text-anchor="middle" font-family="Lato, sans-serif" font-weight="700" font-size="38" fill="#fff">$</text></svg>
  <p>We can close quickly and we buy with Cash...</p>
  <div class="btn-outline" style="left:95px">READ MORE</div>
</section>
<div class="divider" style="left:769px"></div>

<section class="abs service" style="left:793px">
  <h3 class="script">Your <b>Neighborhood</b></h3>
  <svg class="icon" style="left:109px" width="82" height="82" viewBox="0 0 82 82"><circle cx="41" cy="41" r="38" fill="none" stroke="#2f5a80" stroke-width="3.5"/><path d="M22 44l19-13 19 13v10H22z" fill="#2f5a80"/><rect x="36" y="45" width="4" height="4" fill="#fff"/><rect x="42" y="45" width="4" height="4" fill="#fff"/></svg>
  <p>We only buy and renovate homes in our neighborhoods right here in the Morris County, NJ area...</p>
  <div class="btn-outline" style="left:90px">READ MORE</div>
</section>

<section class="abs contact-band">
  <svg class="contact-shape" width="340" height="156" viewBox="0 0 340 156"><path d="M0 0h300l36 78-36 78H0z" fill="#2fa3e0"/></svg>
  <h2 class="contact-title script">Get In<br>Touch</h2>
  <div class="field" style="left:386px;top:26px;width:227px;height:45px">Enter Name</div>
  <div class="field" style="left:637px;top:26px;width:229px;height:45px">Enter Contact No.</div>
  <div class="field" style="left:887px;top:26px;width:228px;height:45px">Enter Email Id</div>
  <div class="field" style="left:386px;top:80px;width:480px;height:50px">Message</div>
  <div class="submit">SUBMIT</div>
</section>

<h4 class="abs script foot-head" style="left:80px">Contact <b>Info</b></h4>
<div class="foot-row" style="left:76px;top:2103px">
  <svg width="24" height="24" viewBox="0 0 24 24"><path d="M22 2L2 11l9 2 2 9z" fill="#888"/></svg>
  <div><strong>Pinecrest Holdings Group</strong><br>Morris County,<br>&nbsp;&nbsp;&nbsp;NJ | 555-014-7723</div>
</div>
<div class="foot-row" style="left:78px;top:2205px">
  <svg width="20" height="20" viewBox="0 0 20 20"><path d="M4 1l4 4-2 3c1 3 3 5 6 6l3-2 4 4-3 3C8 19 1 12 1 4z" fill="#888"/></svg>
  <div>+(123) 456 1212</div>
</div>
<div class="foot-row" style="left:78px;top:2246px">
  <svg width="20" height="20" viewBox="0 0 20 20"><rect x="1" y="4" width="18" height="13" rx="2" fill="none" stroke="#888" stroke-width="1.6"/><path d="M2 5l8 6 8-6" fill="none" stroke="#888" stroke-width="1.6"/></svg>
  <div>hello@pinecrestholdingsgroup.example</div>
</div>

<div class="abs foot-brand">
  <div class="mark"></div>
  <div class="name">PINECREST<br>HOLDINGS GROUP</div>
</div>
<p class="abs foot-tagline">We bring excellence to the home buying and renovation business.</p>

<h4 class="abs script foot-head" style="left:882px">Follow <b>Us On</b></h4>
<div class="social-row first" style="top:2111px"><div class="dot filled"></div><span>Friendbook</span></div>
<div class="social-row" style="top:2175px"><div class="dot"></div><span>Chirper</span></div>
<div class="social-row" style="top:2237px"><div class="dot"></div><span>WorkLink</span></div>

<footer class="abs copyright">Copyright 2016 ~<strong>Pinecrest Holdings Group</strong>~All rights reserved.</footer>

</body>
</html>
```